Stationery and Business Card Design

We need stationary design for our new company lanternfold. Lanternfold is a company that provides city apartment rentals for tourists in Athens We need business cards, letterheads for A4 and A5 and envelopes for A4 A5. The design needs to be modern, friendly and corporate.

Target Market(s)

City Tourists

Industry/Entity Type

Tourism

```html
<!DOCTYPE html>
<html lang="en">
<head>
<meta charset="utf-8">
<title>Lanternfold Stationery</title>
<link rel="stylesheet" href="https://fonts.googleapis.com/css2?family=Montserrat:wght@400;600&family=Tinos:ital@0;1&display=swap">
<style>
  :root {
    --brand: #8e0050;
    --brand-faint: #f4e7ef;
    --paper: #ffffff;
    --ink: #2b2b2b;
    --ink-soft: #555555;
    --bg-top: #5f5f5f;
    --bg-bottom: #3d3d3d;
  }
  * { box-sizing: border-box; margin: 0; padding: 0; }
  html, body { width: 1200px; height: 1200px; overflow: hidden; }
  body {
    position: relative;
    background: linear-gradient(180deg, var(--bg-top), var(--bg-bottom));
    font-family: "Montserrat", sans-serif;
    color: var(--ink);
  }
  .sheet { position: absolute; background: var(--paper); box-shadow: 0 4px 14px rgba(0,0,0,.35); overflow: hidden; }

  .brand-mark { position: absolute; background: var(--brand); }
  .brand-name { position: absolute; font-family: "Montserrat", sans-serif; font-weight: 400; color: var(--brand); white-space: nowrap; letter-spacing: -0.02em; }

  /* Letter */
  .letterhead { left: 66px; top: 180px; width: 481px; height: 682px; }
  .letterhead .brand-mark { left: 224px; top: 22px; width: 32px; height: 32px; }
  .letterhead .brand-name { left: 0; right: 0; top: 56px; text-align: center; font-size: 22px; }
  .letter-body {
    position: absolute; left: 60px; top: 130px; width: 358px;
    font-family: "Tinos", serif; font-size: 9.2px; line-height: 11.7px; color: var(--ink);
    text-align: justify;
  }
  .letter-body p { margin-bottom: 11.5px; }
  .letter-body .closing { margin-top: 52px; margin-bottom: 0; text-align: left; }
  .signature { width: 70px; height: 26px; margin: 2px 0 4px; background: linear-gradient(90deg, #d8d8d8, #f0f0f0); }
  .letter-footer { position: absolute; left: 0; bottom: 0; width: 100%; height: 48px; background: var(--brand); color: #fff; }
  .footer-mark { position: absolute; left: 41px; top: 13px; width: 24px; height: 24px; border: 3px solid #fff; }
  .footer-block { position: absolute; top: 14px; font-size: 6.2px; line-height: 8.2px; }
  .footer-block strong { font-weight: 600; }
  .footer-address { left: 85px; }
  .footer-contacts { left: 178px; }
  .footer-contacts .row { display: flex; align-items: center; gap: 12px; }
  .footer-rule { position: absolute; left: 321px; right: 0; top: 21px; height: 1px; background: rgba(255,255,255,.7); }

  .icon { width: 6px; height: 6px; flex: none; }

  /* Envelope */
  .envelope { left: 631px; top: 180px; width: 495px; height: 701px; }
  .envelope-flap { position: absolute; left: 0; top: 0; }
  .envelope .brand-mark { left: 233px; top: 18px; width: 28px; height: 28px; background: #fff; }
  .envelope .brand-name { left: 0; right: 0; top: 49px; text-align: center; font-size: 19px; color: #fff; }

  /* Blank letterhead */
  .letterhead-blank { left: 578px; top: 261px; width: 496px; height: 701px; }
  .letterhead-blank .brand-mark { left: 78px; top: 39px; width: 30px; height: 30px; }
  .letterhead-blank .brand-name { left: 45px; top: 72px; font-size: 20px; }
  .sender { position: absolute; left: 46px; top: 129px; font-size: 6.3px; line-height: 9.6px; color: var(--ink-soft); }
  .sender .contacts { margin-top: 4px; }
  .sender .row, .card-details .row { display: flex; align-items: center; gap: 13px; }
  .corner-decor { position: absolute; left: 260px; top: 471px; width: 199px; height: 230px; background: linear-gradient(180deg, rgba(244,231,239,0), var(--brand-faint)); }

  /* Business cards */
  .card { top: 881px; width: 234px; height: 130px; }
  .card-front { left: 66px; }
  .card-back { left: 313px; }
  .card-front .brand-mark { left: 51px; top: 45px; width: 21px; height: 21px; }
  .card-front .brand-name { left: 25px; top: 69px; font-size: 13.5px; }
  .card-details { position: absolute; left: 116px; top: 26px; font-size: 5.2px; line-height: 8.2px; color: var(--ink-soft); }
  .card-person { font-size: 7.6px; font-weight: 600; color: var(--ink); line-height: 10px; }
  .card-role { color: var(--brand); margin-bottom: 4px; }
  .card-details .address { margin-bottom: 5px; }
  .card-details .row { gap: 8px; }
  .card-back .brand-mark { left: 103px; top: 40px; width: 26px; height: 26px; }
  .card-back .brand-name { left: 0; right: 0; top: 67px; text-align: center; font-size: 17px; }
</style>
</head>
<body>

<svg width="0" height="0" style="position:absolute" aria-hidden="true">
  <defs>
    <symbol id="i-phone" viewBox="0 0 10 10"><path d="M1 3.5 Q5 0.5 9 3.5 L8 5 L6.5 4.2 V3.3 Q5 2.8 3.5 3.3 V4.2 L2 5 Z M2.5 6 H7.5 V9 H2.5 Z" fill="currentColor"/></symbol>
    <symbol id="i-mobile" viewBox="0 0 10 10"><rect x="3" y="0.8" width="4" height="8.4" rx="0.8" fill="none" stroke="currentColor" stroke-width="1"/></symbol>
    <symbol id="i-mail" viewBox="0 0 10 10"><rect x="0.8" y="2" width="8.4" height="6" fill="none" stroke="currentColor" stroke-width="1"/><path d="M0.8 2 L5 5.5 L9.2 2" fill="none" stroke="currentColor" stroke-width="1"/></symbol>
    <symbol id="i-web" viewBox="0 0 10 10"><circle cx="5" cy="5" r="4.2" fill="none" stroke="currentColor" stroke-width="1"/><path d="M0.8 5 H9.2 M5 0.8 Q2.5 5 5 9.2 M5 0.8 Q7.5 5 5 9.2" fill="none" stroke="currentColor" stroke-width="0.8"/></symbol>
  </defs>
</svg>

<!-- Envelope -->
<div class="sheet envelope">
  <svg class="envelope-flap" width="495" height="100" viewBox="0 0 495 100" aria-hidden="true">
    <path d="M0 0 H495 L470 84 Q465 96 450 96 H28 Z" fill="var(--brand)"/>
  </svg>
  <div class="brand-mark"></div>
  <div class="brand-name">Lanternfold</div>
</div>

<!-- Blank letterhead -->
<div class="sheet letterhead-blank">
  <div class="brand-mark"></div>
  <div class="brand-name">Lanternfold</div>
  <div class="sender">
    <div>14 Orion Lane, Kessington</div>
    <div>Athens 10552</div>
    <div class="contacts">
      <div class="row"><svg class="icon" style="color:var(--brand)"><use href="#i-phone"/></svg>555 214 3080</div>
      <div class="row"><svg class="icon" style="color:var(--brand)"><use href="#i-mail"/></svg>info@lanternfoldapartments.com</div>
      <div class="row"><svg class="icon" style="color:var(--brand)"><use href="#i-web"/></svg>www.lanternfoldapartments.com</div>
    </div>
  </div>
  <div class="corner-decor"></div>
</div>

<!-- Letterhead with letter -->
<div class="sheet letterhead">
  <div class="brand-mark"></div>
  <div class="brand-name">Lanternfold</div>
  <div class="letter-body">
    <p>Gentlemen,</p>
    <p>Enclosed I have the honor to send you an article which I should be pleased if you would accept for the "Northern Quarterly". I am <em>desperately</em> pushed for money; and in the event of Mr. Hadley's liking the "Landscape-Garden", I would take it as an especial favor if you would mail me the amount due for it, so as to reach me here by the 21st, on which day I shall need it. Can you possibly oblige me in this? If you accept the paper I presume you will allow me your usual sum, whatever that is for similar contributions—but I set no price—leaving all to your own liberality. The piece will make 8 of your pages and rather more.</p>
    <p>Will you be kind enough to put the best possible interpretation upon my behavior while in the city? You must have conceived a <em>queer</em> idea of me—but the simple truth is that Brennan would insist upon <em>the juleps</em>, and I knew not what I was either doing or saying. The Review of Ashcombe which I offered you was deficient in a 1/2 page of commencement, which I had written to supersede the old beginning, and which gave the article the character of a general and retrospective review. No wonder you did not take it—I would have been very much mortified if you had. I hope to see you at some future time, under better auspices.</p>
    <p class="closing">In the meantime I remain<br>Yours very truly,</p>
    <div class="signature" role="img" aria-label="Handwritten signature"></div>
    <p>Elias Marlowe</p>
  </div>
  <div class="letter-footer">
    <div class="footer-mark"></div>
    <div class="footer-block footer-address">
      <strong>Lanternfold Apartments</strong><br>14 Orion Lane, Kessington<br>Athens 10552
    </div>
    <div class="footer-block footer-contacts">
      <div class="row"><svg class="icon"><use href="#i-phone"/></svg>555 214 3080</div>
      <div class="row"><svg class="icon"><use href="#i-mail"/></svg>info@lanternfoldapartments.com</div>
      <div class="row"><svg class="icon"><use href="#i-web"/></svg>www.lanternfoldapartments.com</div>
    </div>
    <div class="footer-rule"></div>
  </div>
</div>

<!-- Business card front -->
<div class="sheet card card-front">
  <div class="brand-mark"></div>
  <div class="brand-name">Lanternfold</div>
  <div class="card-details">
    <div class="card-person">Marcus Delaney</div>
    <div class="card-role">President</div>
    <div class="address">14 Orion Lane, Kessington<br>Athens 10552</div>
    <div class="row"><svg class="icon" style="color:var(--brand)"><use href="#i-phone"/></svg>555 214 3080</div>
    <div class="row"><svg class="icon" style="color:var(--brand)"><use href="#i-mobile"/></svg>555 214 3082</div>
    <div class="row"><svg class="icon" style="color:var(--brand)"><use href="#i-mail"/></svg>info@lanternfoldapartments.com</div>
    <div class="row"><svg class="icon" style="color:var(--brand)"><use href="#i-web"/></svg>www.lanternfoldapartments.com</div>
  </div>
</div>

<!-- Business card back -->
<div class="sheet card card-back">
  <div class="brand-mark"></div>
  <div class="brand-name">Lanternfold</div>
</div>

</body>
</html>
```